Business Card- Can you make it cool vs boring!

Need a refresh on my business card! Want it to be modern but simple, classic and a pop of coolness! we do senior living and it is boring. but that doesn't mean our business card have to look boring! Open to two sided cards. our website is www.Dunmere-PK.com

Target Market(s)

capital market

Industry/Entity Type

senior housing/ real estate

Contact Information for Business Card

logo/ name/ cell/ address/ www.Dunmere-PK.com/ space for a QR code

Requirements
Must have
• maybe a QR code (do not make prominent I may not use the QR so design where it can be taken out) that link to more about us/ landing page. needs to be modern but clean
Should not have
• clip art or script

```html
<!DOCTYPE html>
<html lang="en">
<head>
<meta charset="utf-8">
<title>Dunmere Living – Business Card</title>
<link rel="stylesheet" href="https://fonts.googleapis.com/css2?family=Poppins:wght@400;500&family=Yellowtail&display=swap">
<style>
  :root {
    --backdrop: #a5a2a3;
    --card-white: #ffffff;
    --brand-rust: #ae5024;
    --rust-dark: #8f3f1a;
    --rust-light: #c8622e;
    --swoosh-grey: #86858a;
    --text-grey: #727176;
    --divider: #d9d9d9;
  }
  * { margin: 0; padding: 0; box-sizing: border-box; }
  html, body {
    width: 1093px; height: 1200px; overflow: hidden;
    background: var(--backdrop);
    font-family: "Poppins", sans-serif;
  }
  .canvas { position: relative; width: 1093px; height: 1200px; }

  .card {
    position: absolute; left: 264px; width: 580px; height: 356px;
    border-radius: 24px; overflow: hidden;
  }
  .card--front { top: 226px; background: var(--card-white); }
  .card--back {
    top: 620px;
    background: linear-gradient(135deg, var(--rust-dark) 0%, var(--brand-rust) 45%, var(--rust-light) 100%);
  }

  .front-band { position: absolute; left: 0; top: 0; width: 580px; height: 356px; }

  .brand-name {
    position: absolute; left: 0; width: 293px; top: 160px;
    text-align: center; font-weight: 500; font-size: 28px;
    color: var(--brand-rust); letter-spacing: 0.5px;
  }

  .divider {
    position: absolute; left: 293px; top: 71px; width: 1px; height: 208px;
    background: var(--divider);
  }

  .contact { position: absolute; left: 313px; top: 0; color: var(--text-grey); }
  .contact__name {
    position: absolute; top: 72px; left: 0; white-space: nowrap;
    font-family: "Yellowtail", cursive; font-size: 34px; color: var(--brand-rust);
  }
  .contact__title { position: absolute; top: 108px; left: 0; white-space: nowrap; font-size: 16px; }
  .contact__list { position: absolute; top: 144px; left: 0; list-style: none; }
  .contact__item {
    display: flex; align-items: center; gap: 7px;
    height: 21px; font-size: 16px; white-space: nowrap;
  }
  .contact__item svg { width: 15px; height: 15px; flex: none; }
  .contact__accent { color: var(--brand-rust); }
  .contact__address {
    position: absolute; top: 219px; left: 1px; font-size: 16px; line-height: 21px; white-space: nowrap;
  }

  .back-name {
    position: absolute; left: 384px; top: 218px; width: 130px;
    text-align: center; font-weight: 500; font-size: 17px; color: var(--card-white);
  }
</style>
</head>
<body>
<main class="canvas">
  <section class="card card--front" aria-label="Card front">
    <svg class="front-band" viewBox="0 0 580 356" aria-hidden="true">
      <path fill="var(--swoosh-grey)" d="M57,283 C250,322 440,340 492,336 C540,332 566,312 580,301 L580,314 C562,328 532,342 482,343 C420,345 250,326 57,283Z"/>
      <path fill="var(--brand-rust)" d="M0,275 C200,321 420,352 482,349 C540,347 566,333 580,321 L580,356 L0,356Z"/>
    </svg>

    <div class="brand-name">Dunmere Living</div>
    <div class="divider"></div>

    <div class="contact">
      <div class="contact__name">Marcus Hale</div>
      <div class="contact__title">Managing Director</div>
      <ul class="contact__list">
        <li class="contact__item">
          <svg viewBox="0 0 24 24"><path fill="var(--brand-rust)" d="M6.6 10.8a15 15 0 0 0 6.6 6.6l2.2-2.2c.3-.3.7-.4 1-.2 1.1.4 2.3.6 3.6.6.6 0 1 .4 1 1V20c0 .6-.4 1-1 1A17 17 0 0 1 3 4c0-.6.4-1 1-1h3.5c.6 0 1 .4 1 1 0 1.3.2 2.5.6 3.6.1.3 0 .7-.2 1z"/></svg>
          <span>044-987 654 321</span>
        </li>
        <li class="contact__item">
          <svg viewBox="0 0 24 24"><path fill="var(--brand-rust)" d="M2 5h20v14H2z"/><path fill="none" stroke="#fff" stroke-width="1.6" d="M2 5l10 8 10-8M2 19l7.5-7M22 19l-7.5-7"/></svg>
          <span>hello@dunmere-pk.com</span>
        </li>
        <li class="contact__item">
          <svg viewBox="0 0 24 24"><g fill="none" stroke="var(--brand-rust)" stroke-width="2"><circle cx="12" cy="12" r="9"/><ellipse cx="12" cy="12" rx="4" ry="9"/><path d="M3 12h18M5 7h14M5 17h14"/></g></svg>
          <span>www.<span class="contact__accent">Dunmere-PK</span>.com</span>
        </li>
      </ul>
      <p class="contact__address">421, Address line goes here<br>45452,Country Name</p>
    </div>
  </section>

  <section class="card card--back" role="img" aria-label="Card back: repeating diagonal brand pattern in rust tones">
    <div class="back-name">Dunmere Living</div>
  </section>
</main>
</body>
</html>
```